VELTMORN Construction Services
Project: Stationary
Stationary
Simple
Marcus Tendley
marcus@vtmbuilds.example
www.vtmbuilds.example
Finalized Draft of the logo can be seen on the following URL: http://www.quillspark.example/contests/business-logo-264. AI file will be uploaded soon. At the front of the business card the following text should be added design.engineer.build commercial.residential

```html
<!DOCTYPE html>
<html lang="en">
<head>
<meta charset="utf-8">
<title>VELTMORN Construction Services – Stationery</title>
<link rel="stylesheet" href="https://fonts.googleapis.com/css2?family=Questrial&display=swap">
<style>
  :root {
    --page: #ffffff;
    --ink: #3a3a3a;
    --grey: #8a8a8a;
    --green: #8dc63f;
    --black: #000000;
    --white: #ffffff;
    --edge: #9a9a9a;
  }
  * { box-sizing: border-box; margin: 0; padding: 0; }
  html, body { width: 1200px; height: 749px; overflow: hidden; background: var(--page); }
  body { position: relative; font-family: "Questrial", "Century Gothic", sans-serif; }

  .card { position: absolute; width: 525px; height: 300px; overflow: hidden; }
  .card--front { left: 68px; top: 63px; background: var(--white); border: 1px solid var(--edge); }
  .card--white { left: 625px; top: 63px; background: var(--white); border: 1px solid var(--edge); }
  .card--black { left: 68px; top: 380px; background: var(--black); }
  .card--green { left: 625px; top: 380px; background: var(--green); }

  .wordmark { position: absolute; display: flex; flex-direction: column; align-items: center; }
  .wordmark__dot { width: 78px; height: 78px; border-radius: 50%; background: var(--grey); margin-bottom: 14px; }
  .wordmark__name { font-size: 50px; letter-spacing: 2px; line-height: 1; }
  .wordmark__tag { font-size: 11px; letter-spacing: 3.5px; text-transform: uppercase; margin-top: 6px; color: var(--green); }

  .card--white .wordmark, .card--black .wordmark, .card--green .wordmark {
    left: 0; right: 0; top: 42px;
  }
  .card--white .wordmark { color: var(--ink); }
  .card--black .wordmark { color: var(--white); }
  .card--green .wordmark { color: var(--white); }
  .card--green .wordmark__tag { color: var(--white); }
  .card--green .wordmark__dot { background: var(--white); opacity: .85; }

  .card--front .wordmark { left: 18px; top: 14px; color: var(--ink); }
  .card--front .wordmark__dot { width: 68px; height: 68px; margin-bottom: 8px; }
  .card--front .wordmark__name { font-size: 38px; letter-spacing: 1px; }
  .card--front .wordmark__tag { font-size: 9px; letter-spacing: 2.5px; }

  .swoosh { position: absolute; left: 0; top: 0; width: 525px; height: 300px; }

  .holder { position: absolute; right: 40px; top: 150px; font-size: 19px; color: var(--green); }
  .contact { position: absolute; left: 18px; top: 226px; font-size: 12px; line-height: 17px; color: var(--white); list-style: none; }
  .services { position: absolute; right: 16px; top: 262px; font-size: 13px; color: var(--white); letter-spacing: .2px; text-align: right; line-height: 16px; }
</style>
</head>
<body>

<section class="card card--front" aria-label="Business card front">
  <svg class="swoosh" viewBox="0 0 525 300" aria-hidden="true">
    <defs>
      <linearGradient id="greenFade" x1="0" y1="0" x2="1" y2="0">
        <stop offset="0" stop-color="#7fb536"/>
        <stop offset="1" stop-color="#a6d65a"/>
      </linearGradient>
      <linearGradient id="greyFade" x1="0" y1="0" x2="1" y2="0">
        <stop offset="0" stop-color="#9a9a9a"/>
        <stop offset="1" stop-color="#c8c8c8"/>
      </linearGradient>
    </defs>
    <path d="M0 196 C120 174 200 238 330 212 C420 196 480 180 525 184 L525 300 L0 300 Z" fill="url(#greyFade)"/>
    <path d="M0 216 C120 196 200 258 330 232 C420 216 480 202 525 206 L525 300 L0 300 Z" fill="url(#greenFade)"/>
  </svg>

  <div class="wordmark">
    <span class="wordmark__dot"></span>
    <span class="wordmark__name">VELTMORN</span>
    <span class="wordmark__tag">Construction Services</span>
  </div>

  <p class="holder">Marcus Tendley</p>
  <ul class="contact">
    <li>Phone: 555-010-4417</li>
    <li>Email: marcus@vtmbuilds.example</li>
    <li>www.vtmbuilds.example</li>
  </ul>
  <p class="services">design.engineer.build<br>commercial.residential</p>
</section>

<section class="card card--white" aria-label="Logo card on white">
  <div class="wordmark">
    <span class="wordmark__dot"></span>
    <span class="wordmark__name">VELTMORN</span>
    <span class="wordmark__tag">Construction Services</span>
  </div>
</section>

<section class="card card--black" aria-label="Logo card on black">
  <div class="wordmark">
    <span class="wordmark__dot"></span>
    <span class="wordmark__name">VELTMORN</span>
    <span class="wordmark__tag">Construction Services</span>
  </div>
</section>

<section class="card card--green" aria-label="Logo card on green">
  <div class="wordmark">
    <span class="wordmark__dot"></span>
    <span class="wordmark__name">VELTMORN</span>
    <span class="wordmark__tag">Construction Services</span>
  </div>
</section>

</body>
</html>
```